Dunmore Roofing

Want a professional looking business card

Industry/Entity Type

Business

Contact Information for Business Card

Paul Dunmore ( Owner) paul@dunmoreroofing-example.com, www.dunmoreroofing-example.com, Adress: 4172 Township road 43 Greenfield,ON K9X4T2

```html
<!DOCTYPE html>
<html lang="en">
<head>
<meta charset="utf-8">
<title>Dunmore Roofing – Business Card</title>
<link rel="stylesheet" href="https://fonts.googleapis.com/css2?family=Open+Sans:wght@400;600;700&display=swap">
<style>
  :root{
    --page:#2b2b2d;
    --card-grey:#77787b;
    --band-grey:#7d7e81;
    --brand-blue:#1a4586;
    --white:#ffffff;
    --ink-light:#f2f2f2;
  }
  *{box-sizing:border-box;margin:0;padding:0}
  html,body{width:1200px;height:900px;overflow:hidden}
  body{background:var(--page);font-family:"Open Sans",Arial,sans-serif;position:relative}

  .card{position:absolute;width:540px;height:309px;overflow:hidden;
        box-shadow:0 10px 30px rgba(0,0,0,.45)}

  /* back face */
  .card-back{left:40px;top:296px;background:var(--card-grey)}
  .card-back .brand-name{position:absolute;left:0;right:0;top:108px;text-align:center;
        color:var(--white);font-weight:700;font-size:34px;letter-spacing:1px}
  .card-back .web{position:absolute;left:0;right:0;bottom:40px;text-align:center;
        color:var(--ink-light);font-size:13px}

  /* front face */
  .card-front{left:620px;top:296px;background:var(--white)}
  .card-front .brand-name{position:absolute;left:0;right:0;top:60px;text-align:center;
        color:var(--brand-blue);font-weight:700;font-size:34px;letter-spacing:1px}
  .contact-band{position:absolute;right:0;top:118px;width:300px;height:82px;
        background:var(--band-grey);clip-path:polygon(20px 0,100% 0,100% 100%,0 100%)}
  .contact-list{position:absolute;left:34px;top:10px;list-style:none;color:var(--white);
        font-size:12px;line-height:20px;white-space:nowrap}
  .contact-list li{display:flex;align-items:center;gap:7px}
  .contact-list svg{width:13px;height:13px;flex:none}
  .owner-block{position:absolute;left:0;top:200px;width:262px;height:64px;background:var(--brand-blue)}
  .owner-block::before{content:"";position:absolute;left:130px;top:-7px;border:7px solid transparent;
        border-top:0;border-bottom-color:var(--brand-blue)}
  .owner-name{position:absolute;left:0;right:0;top:10px;text-align:center;color:var(--white);
        font-weight:700;font-size:19px}
  .owner-role{position:absolute;left:0;right:0;top:36px;text-align:center;color:var(--white);font-size:13px}
  .address{position:absolute;left:0;right:0;bottom:14px;text-align:center;color:var(--brand-blue);font-size:14px}
</style>
</head>
<body>
  <section class="card card-back" aria-label="Business card back">
    <p class="brand-name">DUNMORE ROOFING</p>
    <p class="web">www.dunmoreroofing-example.com</p>
  </section>

  <section class="card card-front" aria-label="Business card front">
    <p class="brand-name">DUNMORE ROOFING</p>

    <div class="contact-band">
      <ul class="contact-list">
        <li><svg viewBox="0 0 14 14"><rect width="14" height="14" rx="2" fill="#1a4586"/><path d="M4 3.5l1.6-.4 1 2.2-1 .7a5 5 0 0 0 2.4 2.4l.7-1 2.2 1-.4 1.6C7 10 4 7 4 3.5z" fill="#fff"/></svg>(613) 555-0142</li>
        <li><svg viewBox="0 0 14 14"><rect width="14" height="14" rx="2" fill="#1a4586"/><rect x="3" y="4.5" width="8" height="5.5" fill="none" stroke="#fff" stroke-width="1"/><path d="M3 4.5l4 3 4-3" fill="none" stroke="#fff" stroke-width="1"/></svg>paul@dunmoreroofing-example.com</li>
        <li><svg viewBox="0 0 14 14"><rect width="14" height="14" rx="2" fill="#1a4586"/><circle cx="7" cy="7" r="4" fill="none" stroke="#fff" stroke-width="1"/><path d="M3 7h8M7 3c-2 2.5-2 5.5 0 8M7 3c2 2.5 2 5.5 0 8" fill="none" stroke="#fff" stroke-width=".8"/></svg>www.dunmoreroofing-example.com</li>
      </ul>
    </div>

    <div class="owner-block">
      <p class="owner-name">Paul Dunmore</p>
      <p class="owner-role">Owner</p>
    </div>

    <p class="address">4172 Township road 43, Greenfield,ON K9X4T2</p>
  </section>
</body>
</html>
```